Puffy Clouds Cotton Candy

Looking for a logo design and business cards to help a 13 year old entrepreneur promote her cotton candy business.
Contact Information for Business Card
Name, Phone & Email
Colors
E54698
E96AAD
F1A4CE
F9D9EA
FCEFF6
A7469A
B969AE
D3A5CF
EDDBEB
F8F0F9
6B429C
8869AF
B7A5CE
E3DAEB
F3F0F8
Requirements
Must have
- A fun feel that is appropriate for a teenage girl selling cotton candy

```html
<!DOCTYPE html>
<html lang="en">
<head>
<meta charset="utf-8">
<title>Puffy Clouds Cotton Candy – Business Cards</title>
<link rel="stylesheet" href="https://fonts.googleapis.com/css2?family=Fredoka:wght@500;600&family=Nunito:wght@700&display=swap">
<style>
  :root {
    --pink: #E54698;
    --pink-soft: #E96AAD;
    --plum: #A7469A;
    --violet: #6B429C;
    --card-white: #FFFFFF;
    --backdrop: #A99886;
  }
  * { margin: 0; padding: 0; box-sizing: border-box; }
  html, body { width: 1200px; height: 1200px; overflow: hidden; }
  body { background: var(--backdrop); position: relative; font-family: "Nunito", sans-serif; }

  .card {
    position: absolute;
    top: 480px;
    width: 420px;
    height: 240px;
    border-radius: 19px;
    overflow: hidden;
  }
  .card--front { left: 155px; background: var(--card-white); }
  .card--back  { left: 624px; background: var(--pink); }

  .brand-name {
    position: absolute;
    font-family: "Fredoka", sans-serif;
    font-weight: 600;
    line-height: 0.95;
    display: flex;
    align-items: flex-start;
    gap: 8px;
  }
  .brand-name__dot {
    flex: none;
    border-radius: 50%;
  }
  .card--front .brand-name { left: 30px; top: 34px; font-size: 28px; color: var(--plum); }
  .card--front .brand-name__dot { width: 12px; height: 12px; background: var(--pink); margin-top: 6px; }
  .card--back .brand-name { left: 40px; top: 42px; font-size: 50px; color: var(--card-white); }
  .card--back .brand-name__dot { width: 20px; height: 20px; background: var(--card-white); margin-top: 12px; }

  .holder-name {
    position: absolute;
    left: 50px;
    top: 154px;
    font-family: "Fredoka", sans-serif;
    font-weight: 600;
    font-size: 19px;
    color: var(--pink);
  }
  .holder-rule {
    position: absolute;
    left: 180px;
    right: 0;
    top: 165px;
    height: 1.5px;
    background: var(--violet);
  }
  .contact-list {
    position: absolute;
    left: 50px;
    top: 190px;
    list-style: none;
  }
  .contact-list li {
    display: flex;
    align-items: center;
    gap: 8px;
    height: 15px;
    font-size: 11.5px;
    color: var(--violet);
  }
  .contact-list svg { width: 14px; height: 12px; flex: none; }
</style>
</head>
<body>
  <section class="card card--front">
    <div class="brand-name">
      <span>Puffy Clouds<br>Cotton Candy</span>
      <span class="brand-name__dot"></span>
    </div>
    <p class="holder-name">Maya Lane</p>
    <div class="holder-rule"></div>
    <ul class="contact-list">
      <li>
        <svg viewBox="0 0 14 12" aria-hidden="true">
          <path d="M3 1.5c1-.6 1.6 0 2.1 1l.5 1c.3.6 0 1-.5 1.3-.3.2-.3.5-.1.9.6 1 1.3 1.7 2.3 2.3.4.2.7.2.9-.1.3-.5.7-.8 1.3-.5l1 .5c1 .5 1.6 1.1 1 2.1-.7 1.1-2 1.4-3.4.8C5.6 9.8 3.6 7.8 2.8 5.3 2.2 3.8 2.1 2.2 3 1.5z" fill="var(--pink)"/>
          <path d="M8 2a3.5 3.5 0 0 1 3.3 3.3M8 .4a5 5 0 0 1 5 5" stroke="var(--pink)" stroke-width="1" fill="none" stroke-linecap="round"/>
        </svg>
        <span>09. 4821. 3067</span>
      </li>
      <li>
        <svg viewBox="0 0 14 12" aria-hidden="true">
          <rect x="0.5" y="1.5" width="13" height="9" fill="var(--pink)"/>
          <path d="M0.8 2l6.2 5 6.2-5M0.8 10.2l4.6-4M13.2 10.2l-4.6-4" stroke="var(--card-white)" stroke-width="1" fill="none"/>
        </svg>
        <span>maya@puffyclouds.com</span>
      </li>
    </ul>
  </section>

  <section class="card card--back">
    <div class="brand-name">
      <span>Puffy Clouds<br>Cotton Candy</span>
      <span class="brand-name__dot"></span>
    </div>
  </section>
</body>
</html>
```